New Business Card Design Project

Use the flyer uploaded and website www.brightoakbuilders.com for inspiration.
List Our Services on Backside of business cards
Marcus Delling
Harborline Builders Inc.
Licensed General Contractors
858-471-6093

Contact Information for Business Card

Use the flyer uploaded and website www.brightoakbuilders.com for inspiration. List Our Services on Backside of business cards Marcus Delling Harborline Builders Inc. Licensed General Contractors 858-471-6093

```html
<!DOCTYPE html>
<html lang="en">
<head>
<meta charset="utf-8">
<title>Harborline Builders – Business Card</title>
<link rel="stylesheet" href="https://fonts.googleapis.com/css2?family=Montserrat:wght@500;600;700&family=Oswald:wght@600&display=swap">
<style>
  :root {
    --page: #e9e7e3;
    --ink: #1b1b1d;
    --white: #ffffff;
    --red: #e5202e;
    --blue: #3a86cc;
  }
  * { box-sizing: border-box; margin: 0; padding: 0; }
  html, body { width: 1200px; height: 900px; overflow: hidden; }
  body {
    background: var(--page);
    font-family: "Montserrat", Arial, sans-serif;
    position: relative;
  }
  .card {
    position: absolute;
    left: 285px;
    width: 630px;
    height: 360px;
    overflow: hidden;
    box-shadow: 0 10px 28px rgba(0,0,0,.22);
  }
  /* ---------- Back side ---------- */
  .card-back { top: 50px; background: var(--ink); color: var(--white); }
  .services-heading {
    position: absolute; top: 58px; left: 0; width: 100%;
    text-align: center;
    color: var(--red);
    font-weight: 700; font-size: 23px; letter-spacing: 1px;
  }
  .services-tag {
    position: absolute; top: 96px; left: 50%; transform: translateX(-50%);
    background: var(--blue);
    padding: 8px 30px;
    font-weight: 600; font-size: 21px; letter-spacing: 1.5px;
    white-space: nowrap;
  }
  .service-list {
    position: absolute; list-style: none;
    font-weight: 600; line-height: 1.45;
  }
  .service-list li { position: relative; padding-left: 18px; white-space: nowrap; }
  .service-list li::before {
    content: ""; position: absolute; left: 0; top: 50%;
    width: 7px; height: 7px; margin-top: -3px; border-radius: 50%;
    background: var(--blue);
  }
  .service-list-main { left: 40px; top: 200px; font-size: 16.5px; }
  .service-list-extra { left: 380px; top: 164px; font-size: 14px; }

  /* ---------- Front side ---------- */
  .card-front { top: 470px; background: var(--white); }
  .front-shapes { position: absolute; inset: 0; }
  .holder-name {
    position: absolute; left: 52px; top: 58px;
    font-family: "Oswald", "Arial Narrow", sans-serif;
    font-weight: 600; font-size: 40px; color: var(--red);
    letter-spacing: .5px; line-height: 1;
  }
  .contact-list {
    position: absolute; left: 54px; top: 120px; list-style: none;
    font-size: 17px; font-weight: 500; color: var(--ink); line-height: 1.4;
  }
  .contact-list li { display: flex; align-items: center; gap: 10px; }
  .contact-list svg { width: 18px; height: 18px; flex: none; }
  .company-lines {
    position: absolute; left: 54px; top: 208px;
    color: var(--red); font-weight: 600; font-size: 17px; line-height: 1.3;
  }
  .brand-name {
    position: absolute; right: 44px; bottom: 40px;
    color: var(--white); font-weight: 600; font-size: 19px; letter-spacing: 1.5px;
  }
</style>
</head>
<body>

<section class="card card-back" aria-label="Back of business card">
  <h2 class="services-heading">OUR SERVICES ARE 100% GUARENTEED</h2>
  <div class="services-tag">SPECIALIZING IN</div>
  <ul class="service-list service-list-main">
    <li>Remodel: Kitchen &amp; Bath</li>
    <li>Painting: Interior &amp; Exterior</li>
    <li>Flooring: Carpet, Vinyl, Wood</li>
    <li>Window &amp; Door Replacement</li>
    <li>Plumbing: Repairs &amp; Upgrades</li>
  </ul>
  <ul class="service-list service-list-extra">
    <li>Energy-Efficient Upgrades</li>
    <li>Deck &amp; Patio Construction</li>
    <li>Water &amp; Mold Damage</li>
    <li>Garage Renovation</li>
  </ul>
</section>

<section class="card card-front" aria-label="Front of business card">
  <svg class="front-shapes" viewBox="0 0 630 360" width="630" height="360">
    <defs>
      <linearGradient id="room-warm" x1="0" y1="0" x2="1" y2="1">
        <stop offset="0" stop-color="#f3ece2"/><stop offset="1" stop-color="#d9b48a"/>
      </linearGradient>
      <linearGradient id="room-cool" x1="0" y1="0" x2="1" y2="1">
        <stop offset="0" stop-color="#f4f6f6"/><stop offset="1" stop-color="#c9d6d4"/>
      </linearGradient>
    </defs>
    <g role="img" aria-label="Photos of remodelled kitchens and bathrooms">
      <rect x="420" y="-40" width="100" height="100" rx="14" transform="rotate(45 470 10)" fill="url(#room-warm)"/>
      <rect x="535" y="-22" width="95" height="95" rx="14" transform="rotate(45 582 25)" fill="url(#room-warm)"/>
      <rect x="388" y="74" width="95" height="95" rx="14" transform="rotate(45 435 121)" fill="url(#room-cool)"/>
      <rect x="495" y="92" width="95" height="95" rx="14" transform="rotate(45 542 139)" fill="url(#room-cool)"/>
    </g>
    <path d="M0 325 C 230 328 430 275 630 145 L630 360 L0 360 Z" fill="var(--ink)"/>
    <path d="M0 314 C 220 318 400 268 540 190" fill="none" stroke="var(--blue)" stroke-width="11"/>
  </svg>

  <h1 class="holder-name">MARCUS DELLING</h1>
  <ul class="contact-list">
    <li>
      <svg viewBox="0 0 24 24" aria-hidden="true"><path d="M6.6 10.8a15 15 0 0 0 6.6 6.6l2.2-2.2c.3-.3.7-.4 1-.2 1.1.4 2.3.6 3.6.6.6 0 1 .4 1 1V20c0 .6-.4 1-1 1A17 17 0 0 1 3 4c0-.6.4-1 1-1h3.5c.6 0 1 .4 1 1 0 1.3.2 2.5.6 3.6.1.3 0 .7-.2 1z" fill="var(--blue)"/></svg>
      858-471-6093
    </li>
    <li>
      <svg viewBox="0 0 24 24" aria-hidden="true"><rect x="2" y="5" width="20" height="14" rx="1" fill="var(--blue)"/><path d="M2 6l10 7 10-7" fill="none" stroke="#fff" stroke-width="1.6"/></svg>
      info@brightoakbuilders.com
    </li>
    <li>
      <svg viewBox="0 0 24 24" aria-hidden="true"><g fill="none" stroke="var(--blue)" stroke-width="1.8"><circle cx="12" cy="12" r="9.5"/><ellipse cx="12" cy="12" rx="4" ry="9.5"/><path d="M2.5 12h19M4 7h16M4 17h16"/></g></svg>
      www.brightoakbuilders.com
    </li>
  </ul>
  <p class="company-lines">Harborline Builders Inc.<br>Licensed General Contractors</p>
  <p class="brand-name">HARBORLINE BUILDERS</p>
</section>

</body>
</html>
```